Website Redesign Project Puzzle Vault Larkfield

We are an escape room company located in Ashburn, Virginia. We currently have a website https://www.puzzlevaultlarkfield.example based upon html/bootstrap/javascript/php/mysql and I'd like to keep it that way. I'm looking for someone upgrade the front page so it is more informative, cleaner, quicker to load, and optimizes the space for full sale opportunities.

Target Market(s)

Corporate Clients, Families, Friends. All ages

Industry/Entity Type

Entertainment Industry

Coding

Coded - Design and coding required

Number of Pages Required

3 page

Font styles to use
Other font styles liked:
• Similar to Facebook or Amazon

Requirements
Must have
• Must be mobile friendly. bootstrap. Lots of graphics (will provide) nice and easy to read fonts. Easy to read layout. Must look clean, fresh, exciting, and want to grab attention.
• Please visit my facebook page and website for more details. facebook.com/puzzlevaultlarkfield
Nice to have
• Same color as existing but open to options if they look nice.
Should not have
• Should not be wordpress or hard to modify.

```html
<!DOCTYPE html>
<html lang="en">
<head>
<meta charset="utf-8">
<title>Puzzle Vault Larkfield</title>
<link href="https://fonts.googleapis.com/css2?family=Lato:wght@400;700;900&display=swap" rel="stylesheet">
<style>
:root{
  --blue:#1a8fe3;
  --blue-dark:#0b5f9e;
  --navy:#06223a;
  --ink:#222;
  --muted:#555;
  --line:#d9d9d9;
  --panel:#f1f1f1;
  --dark:#101010;
  --white:#fff;
}
*{box-sizing:border-box;margin:0;padding:0}
html,body{width:1200px;height:4710px;overflow:hidden}
body{position:relative;font-family:'Lato',Arial,sans-serif;color:var(--ink);background:var(--white)}
.abs{position:absolute}
.btn{position:absolute;background:var(--blue);color:var(--white);font-weight:700;display:flex;align-items:center;justify-content:center;text-transform:none}
/* header */
.site-header{position:absolute;left:0;top:0;width:1200px;height:137px;background:var(--white)}
.brand{position:absolute;left:75px;top:28px;display:flex;align-items:center;gap:12px}
.brand-mark{width:38px;height:38px;background:var(--blue)}
.brand-name{font-weight:900;font-size:22px;line-height:1.05;color:var(--blue);width:170px;text-transform:uppercase}
.nav a{position:absolute;top:68px;font-size:12px;font-weight:700;color:var(--ink);text-decoration:none;letter-spacing:.2px}
.nav-book{left:946px;top:51px;width:180px;height:46px;font-size:16px}
/* hero */
.hero{position:absolute;left:0;top:137px;width:1200px;height:569px;background:linear-gradient(135deg,#2b2219 0%,#15110d 45%,#3a2c22 75%,#120e0b 100%)}
.hero-title{position:absolute;left:0;top:165px;width:1200px;text-align:center;color:var(--white);font-size:58px;font-weight:900;line-height:62px;text-shadow:0 2px 6px rgba(0,0,0,.5)}
.hero-book{left:510px;top:320px;width:180px;height:44px;font-size:16px}
/* rooms */
.room-frame{position:absolute;width:511px;height:287px;border:3px solid #e2e2e2;border-top:none}
.room-frame::before,.room-frame::after{content:"";position:absolute;top:0;width:28px;border-top:3px solid #e2e2e2}
.room-frame::before{left:0}.room-frame::after{right:0}
.room-photo{position:absolute;width:450px;height:223px}
.room-name{position:absolute;font-size:22px;font-weight:900;color:var(--blue)}
.room-diff{position:absolute;font-size:16px;font-weight:700;color:var(--ink);text-align:right;width:200px}
.room-desc{position:absolute;width:440px;font-size:13px;line-height:27px;color:#333}
/* corporate */
.corp-photo{position:absolute;left:0;top:1652px;width:1200px;height:382px;background:linear-gradient(180deg,#7d8790 0%,#6f6a64 40%,#4c7fae 80%,#1f8fe0 100%)}
.corp-band{position:absolute;left:0;top:2034px;width:1200px;height:216px;background:var(--blue)}
.corp-panel{position:absolute;left:75px;top:2034px;width:1050px;height:710px;background:var(--white);border:3px solid #e4e4e4;border-top:none}
.section-title{position:absolute;font-size:36px;font-weight:900;color:var(--ink)}
.corp-box{position:absolute;top:2144px;width:309px;height:239px;background:linear-gradient(180deg,#0c7fcf 0%,#084a7c 50%,#041a2a 100%);color:var(--white);text-align:center}
.corp-box h3{position:absolute;left:10px;right:10px;font-size:27px;line-height:32px;font-weight:900}
.corp-box .btn{left:81px;top:162px;width:148px;height:40px;font-size:16px;font-weight:400}
.form-panel{position:absolute;background:var(--panel)}
.field{position:absolute;background:var(--white);border:1px solid #dedede;font-size:12px;color:#555;padding:0 14px;display:flex;align-items:center}
.field.area{align-items:flex-start;padding-top:14px}
.field.select::after{content:"";position:absolute;right:14px;top:50%;width:0;height:0;border-left:4px solid transparent;border-right:4px solid transparent;border-top:5px solid #333;margin-top:1px}
.field.select::before{content:"";position:absolute;right:14px;top:50%;width:0;height:0;border-left:4px solid transparent;border-right:4px solid transparent;border-bottom:5px solid #333;margin-top:-6px}
.submit{width:146px;height:42px;font-size:16px;font-weight:400}
/* birthday */
.bday{position:absolute;left:0;top:2798px;width:1200px;height:573px;background:var(--dark)}
.bday-photo{position:absolute;left:677px;top:0;width:523px;height:573px;background:linear-gradient(160deg,#b8213a 0%,#3a1b4f 40%,#1d2a5a 70%,#4f4c6b 100%)}
.bday-pointer{position:absolute;left:563px;top:3371px;width:0;height:0;border-left:37px solid transparent;border-right:37px solid transparent;border-top:31px solid var(--dark)}
.bday-title{position:absolute;left:75px;top:2860px;font-size:36px;font-weight:900;color:var(--white)}
.bday-text{position:absolute;left:75px;top:2922px;width:560px;font-size:13px;line-height:28px;color:#e6e6e6}
.bday-box{position:absolute;top:3058px;width:259px;height:192px;background:var(--blue);color:var(--white);text-align:center;padding:22px 10px 0}
.bday-box p{font-size:20px;font-weight:700;line-height:25px}
.bday-box .price{margin-top:14px;font-size:22px;font-weight:900;color:var(--navy);line-height:28px}
.bday-box .price span{color:var(--white)}
.bday-note{position:absolute;left:75px;top:3280px;font-size:13px;font-weight:700;color:var(--white)}
.bday-form{position:absolute;left:75px;top:3444px;width:1050px;height:256px;border:3px solid #e4e4e4;border-top:none;background:var(--white)}
.bday-form::before,.bday-form::after{content:"";position:absolute;top:0;width:28px;border-top:3px solid #e4e4e4}
.bday-form::before{left:0}.bday-form::after{right:0}
/* faq */
.faq{position:absolute;left:0;top:3759px;width:1200px;height:461px;background:#f2f2f2}
.faq-intro{position:absolute;left:90px;top:46px;width:1020px;text-align:center;font-size:23px;line-height:32px;font-weight:700;color:#2a2a2a}
.faq-item{position:absolute;width:512px;height:48px;background:var(--white);color:var(--blue);font-size:13px;font-weight:700;display:flex;align-items:center;padding:0 18px}
.faq-item svg{position:absolute;right:16px;top:17px}
/* contact */
.contact{position:absolute;left:0;top:4220px;width:1200px;height:362px;background:linear-gradient(180deg,#1b1b1b,#0e0e0e)}
.contact-title{position:absolute;left:0;top:52px;width:1200px;text-align:center;font-size:36px;font-weight:900;color:var(--white)}
.contact-line{position:absolute;left:0;width:1200px;display:flex;justify-content:center;align-items:center;gap:12px;color:#eee;font-size:17px}
.contact-btn{left:527px;top:254px;width:146px;height:42px;font-size:16px;font-weight:400}
/* footer */
.site-footer{position:absolute;left:0;top:4582px;width:1200px;height:128px;background:var(--white)}
.copy{position:absolute;left:75px;top:46px;font-size:13px;line-height:23px;color:#333}
.social{position:absolute;right:75px;top:50px;display:flex;gap:22px}
.social span{width:22px;height:22px;background:#333;display:block}
</style>
</head>
<body>

<header class="site-header">
  <div class="brand"><span class="brand-mark"></span><span class="brand-name">Puzzle Vault Larkfield</span></div>
  <nav class="nav">
    <a href="#" style="left:303px">ESCAPE ROOMS</a>
    <a href="#" style="left:441px">SPECIAL EVENTS</a>
    <a href="#" style="left:584px">LOCATIONS</a>
    <a href="#" style="left:696px">HOW IT WORKS</a>
    <a href="#" style="left:835px">CONTACT US</a>
  </nav>
  <a class="btn nav-book" href="#">BOOK NOW</a>
</header>

<section class="hero" role="img" aria-label="Players solving clues inside a dimly lit escape room">
  <h1 class="hero-title">PUZZLE VAULT LARKFIELD<br>VIRGINIA</h1>
  <a class="btn hero-book" href="#">BOOK NOW</a>
</section>

<section class="rooms">
  <div class="room-frame" style="left:75px;top:874px"></div>
  <div class="room-photo" role="img" aria-label="Freight elevator with folding metal gate" style="left:106px;top:770px;background:linear-gradient(180deg,#3a3836,#8a8580 50%,#2d2b29)"></div>
  <div class="room-name" style="left:106px;top:1019px">ELEVATOR</div>
  <div class="room-diff" style="left:356px;top:1024px">Difficulty: 10/10</div>
  <p class="room-desc" style="left:106px;top:1055px">The main elevators are down so you'll need to take the freight elevator to the top floor if you want to get your award. The last celebrity that attempted to do so wasn't so lucky.</p>

  <div class="room-frame" style="left:614px;top:874px"></div>
  <div class="room-photo" role="img" aria-label="Candy shop room with tall jars of colourful sweets" style="left:644px;top:770px;background:linear-gradient(90deg,#9aa4c8,#c9a34a 30%,#8e9ac2 55%,#c46a4a 80%,#9aa4c8)"></div>
  <div class="room-name" style="left:644px;top:1019px">CANDY SHOP</div>
  <div class="room-diff" style="left:888px;top:1024px">Difficulty: 7/10</div>
  <p class="room-desc" style="left:644px;top:1055px">With all of the candy right before your eyes, find the golden ticket and win the prize!</p>

  <div class="room-frame" style="left:75px;top:1308px"></div>
  <div class="room-photo" role="img" aria-label="Close view of a steel bank vault door" style="left:106px;top:1202px;background:linear-gradient(90deg,#3a3c3e,#6c6f72 60%,#45484a)"></div>
  <div class="room-name" style="left:106px;top:1452px">BANK HEIST</div>
  <div class="room-diff" style="left:356px;top:1457px">Difficulty: 8/10</div>
  <p class="room-desc" style="left:106px;top:1488px">With your family held hostage, the mob gave you one choice - rob the bank in exchange for their freedom or its goodbyes forever.</p>

  <div class="room-frame" style="left:614px;top:1308px"></div>
  <div class="room-photo" role="img" aria-label="Group of players in orange jumpsuits inside the jail room" style="left:644px;top:1202px;background:linear-gradient(180deg,#3b3f3c,#c8521f 60%,#9a3b18)"></div>
  <div class="room-name" style="left:644px;top:1452px">JAIL BREAK</div>
  <div class="room-diff" style="left:888px;top:1457px">Difficulty: 8/10</div>
  <p class="room-desc" style="left:644px;top:1488px">One Guard, One Goal: get out.</p>
</section>

<section class="corporate">
  <div class="corp-photo" role="img" aria-label="Large group of guests posing together in the lobby"></div>
  <div class="corp-band"></div>
  <div class="corp-panel"></div>
  <h2 class="section-title" style="left:0;width:1200px;text-align:center;top:2072px">CORPORATE EVENTS</h2>
  <div class="corp-box" style="left:106px"><h3 style="top:50px">On-site multi-room packages</h3><a class="btn" href="#">More Details</a></div>
  <div class="corp-box" style="left:446px"><h3 style="top:34px">Off-site Hot Seat Escape Room package</h3><a class="btn" href="#">More Details</a></div>
  <div class="corp-box" style="left:785px"><h3 style="top:18px">Off-site Customer Escape Room to fit any space you provide us.</h3><a class="btn" href="#">More Details</a></div>
  <div class="form-panel" style="left:106px;top:2414px;width:988px;height:300px"></div>
  <div class="field" style="left:165px;top:2445px;width:210px;height:39px">Name</div>
  <div class="field" style="left:384px;top:2445px;width:210px;height:39px">Phone No</div>
  <div class="field" style="left:605px;top:2445px;width:211px;height:39px">Email Address</div>
  <div class="field select" style="left:825px;top:2445px;width:210px;height:39px">Select package</div>
  <div class="field area" style="left:165px;top:2497px;width:870px;height:126px">Description</div>
  <a class="btn submit" href="#" style="left:527px;top:2639px">Submit</a>
</section>

<section class="bday">
  <div class="bday-photo" role="img" aria-label="Teenagers celebrating a birthday in the neon lit party room"></div>
</section>
<div class="bday-pointer"></div>
<h2 class="bday-title">BIRTHDAY PARTIES</h2>
<p class="bday-text">Celebrate this year in style by treating your family with an escape room birthday package. You and your loved ones have the choice of four escape rooms and will enjoy a private party afterwards in our party room. Either of these packages will be sure to satisfy your needs.</p>
<div class="bday-box" style="left:75px"><p>A private escape room event with party room pizza and soda.</p><p class="price">Add just <span>$150</span> to your escape room.</p></div>
<div class="bday-box" style="left:356px"><p>A private escape room event with a party room rental</p><p class="price">Bring your own food Add just <span>$125</span></p></div>
<p class="bday-note">Note: A $50 cleaning fee applies to all parties who don't clean after themselves</p>

<div class="bday-form"></div>
<div class="field" style="left:100px;top:3477px;width:238px;height:37px">Name</div>
<div class="field select" style="left:348px;top:3477px;width:237px;height:37px">Number</div>
<div class="field select" style="left:100px;top:3526px;width:238px;height:37px">Group size</div>
<div class="field select" style="left:348px;top:3526px;width:237px;height:37px">Which package</div>
<div class="field" style="left:100px;top:3576px;width:485px;height:37px">Email Address</div>
<div class="field area" style="left:613px;top:3477px;width:487px;height:136px">Description</div>
<a class="btn submit" href="#" style="left:527px;top:3633px">Submit</a>

<section class="faq">
  <p class="faq-intro">An escape room is a themed environment where you and your friends must work together to complete the objectives through solving puzzles before time runs out. Most missions will lock you in while some of our missions do not.</p>
  <div class="faq-item" style="left:75px;top:176px">How do I make a reservation?<svg width="14" height="14" viewBox="0 0 14 14"><circle cx="7" cy="7" r="7" fill="#333"/><path d="M5.5 4l3 3-3 3" stroke="#fff" stroke-width="1.6" fill="none"/></svg></div>
  <div class="faq-item" style="left:613px;top:176px">How can I redeem a voucher or promo code?<svg width="14" height="14" viewBox="0 0 14 14"><circle cx="7" cy="7" r="7" fill="#333"/><path d="M5.5 4l3 3-3 3" stroke="#fff" stroke-width="1.6" fill="none"/></svg></div>
  <div class="faq-item" style="left:75px;top:235px">How long does an escape last?<svg width="14" height="14" viewBox="0 0 14 14"><circle cx="7" cy="7" r="7" fill="#333"/><path d="M5.5 4l3 3-3 3" stroke="#fff" stroke-width="1.6" fill="none"/></svg></div>
  <div class="faq-item" style="left:613px;top:235px">Where do I park?<svg width="14" height="14" viewBox="0 0 14 14"><circle cx="7" cy="7" r="7" fill="#333"/><path d="M5.5 4l3 3-3 3" stroke="#fff" stroke-width="1.6" fill="none"/></svg></div>
  <div class="faq-item" style="left:75px;top:294px">Is there an age limit?<svg width="14" height="14" viewBox="0 0 14 14"><circle cx="7" cy="7" r="7" fill="#333"/><path d="M5.5 4l3 3-3 3" stroke="#fff" stroke-width="1.6" fill="none"/></svg></div>
  <div class="faq-item" style="left:613px;top:294px">What is the cancellation policy?<svg width="14" height="14" viewBox="0 0 14 14"><circle cx="7" cy="7" r="7" fill="#333"/><path d="M5.5 4l3 3-3 3" stroke="#fff" stroke-width="1.6" fill="none"/></svg></div>
  <div class="faq-item" style="left:75px;top:353px">I'm pregnant, can I participate?<svg width="14" height="14" viewBox="0 0 14 14"><circle cx="7" cy="7" r="7" fill="#333"/><path d="M5.5 4l3 3-3 3" stroke="#fff" stroke-width="1.6" fill="none"/></svg></div>
  <div class="faq-item" style="left:613px;top:353px">Which room is the most challenging?<svg width="14" height="14" viewBox="0 0 14 14"><circle cx="7" cy="7" r="7" fill="#333"/><path d="M5.5 4l3 3-3 3" stroke="#fff" stroke-width="1.6" fill="none"/></svg></div>
</section>

<section class="contact">
  <h2 class="contact-title">CONTACT US</h2>
  <p class="contact-line" style="top:125px"><svg width="12" height="16" viewBox="0 0 12 16"><path d="M6 0a6 6 0 0 0-6 6c0 4.5 6 10 6 10s6-5.5 6-10a6 6 0 0 0-6-6zm0 8.5A2.5 2.5 0 1 1 6 3.5a2.5 2.5 0 0 1 0 5z" fill="#1a8fe3"/></svg>1180 Larkfield Commons Drive, Suite 210, Larkfield, Va 20150</p>
  <p class="contact-line" style="top:157px"><svg width="15" height="15" viewBox="0 0 16 16"><path d="M3.5 1l2.5 3-1.5 2c1 2 3 4 5 5l2-1.5 3 2.5-1.5 2.5C8 15 1 8 1 2.5z" fill="#1a8fe3"/></svg>(555) 014 2290 &nbsp;|&nbsp; <svg width="16" height="12" viewBox="0 0 16 12"><rect width="16" height="12" rx="1" fill="#1a8fe3"/><path d="M1 1l7 5 7-5" stroke="#101010" stroke-width="1.4" fill="none"/></svg>sales@puzzlevaultlarkfield.example</p>
  <p class="contact-line" style="top:189px"><svg width="15" height="15" viewBox="0 0 16 16"><circle cx="8" cy="8" r="7" stroke="#1a8fe3" stroke-width="1.6" fill="none"/><path d="M8 4v4l3 2" stroke="#1a8fe3" stroke-width="1.6" fill="none"/></svg>Hours: Wednesday - Fridays (4 to 10pm) Weekends (11am to 9pm)</p>
  <a class="btn contact-btn" href="#">Contact Us</a>
</section>

<footer class="site-footer">
  <p class="copy">Copyright © 2019, Company Name<br>All Right reserved</p>
  <div class="social" aria-label="Social media links"><span></span><span></span><span></span><span></span><span></span></div>
</footer>

</body>
</html>
```